Modern & Simple Essential Oils Label

Company Name: Meadowlark Essentials

What we sell: Aromatherapy products, pure therapeutic essential oils.

Design need:
We are looking for a creative and youthful design for the labels used on small essentials oils.

I have two sizes of bottles that I use for essential oils a 5ml bottle and a 15ml bottle. They are dark Amber color glass with black lids. I like the clear labels or mayble a dark brown background. With white or clear lettering with punch of color too! Each oil type is represented by different color. (lavender- purple, lemon - yellow). The label will be the same for all the oils in the two sizes with only a different oil name & coordinating color.
5ml label size should be: 1 " x 2.625"
15ml label size should be: 1.5" x 3.5"

I have some labels that I have had another designer start on, but they aren't quite what I want and missing that something (alot!).. I don't know what. Interest maybe? Lack of design? I dunno.. they are attached. Maybe it's the logo? I don't know! But its gotta change! When I cut out a proof and put a sample on the bottle as I look straight on at the label all I see is a big dot, no logo.. nothing interesting.
Updates

Project Deadline Extended
Reason: Hi! Id like to extend this deadline. Ive been unavailable for a few days due to an illness and Im so far behind! Im feeling MUCH better and looking forward to getting caught up and move with the project. Im not sure how this works, but I attached a list of the oils that we currently have available. And in the list is the idea for the color schemes for the oils. The basic idea is for it to have a wide array of colors, so using different shades of greens, yellows, oranges and so on. So that its like a rainbow. We are not set of that particular color for that particular oil. It was just a idea list of possible colors for oils. Thanks so much!

Target Market(s)

Metro & Modern people. Interested in healthy organic living, Mostly women (some men) 20-45 who are interested in holistic healing.

Industry/Entity Type

It Company

Requirements
Must have
• A reputable look. Clean, organic, crisp, zen or spa-like feel. Modern, youthful appealing label design. Approachable and interesting, not intimidating so that I don't turn away people who are new or not familiar with how to use essential oils.
Should not have
• do NOT want the look to be anywhere close to medicinal, witchy, crafty, hippie, mystical, overly earthy, magical, or voodoo. Do not want it to look like something out of a grandmothers medicine cabinet.

```html
<!DOCTYPE html>
<html lang="en">
<head>
<meta charset="utf-8">
<title>Rosemary Essential Oil Label – Meadowlark Essentials</title>
<link rel="stylesheet" href="https://fonts.googleapis.com/css2?family=Archivo+Narrow:wght@400;700&family=Arimo:wght@700&family=Lato:ital,wght@0,300;0,700;1,900&family=Yellowtail&display=swap">
<style>
  :root {
    --page: #ffffff;
    --back-panel: #efeeee;
    --oil-red: #d13232;
    --ink-grey: #8a8a8a;
    --ink-white: #ffffff;
    --logo-blush: #f6dcdc;
    --fold-line: #555555;
  }
  html, body {
    margin: 0;
    padding: 0;
    width: 1200px;
    height: 591px;
    overflow: hidden;
    background: var(--page);
  }
  .label {
    position: relative;
    width: 1200px;
    height: 591px;
  }
  .back-panel {
    position: absolute;
    left: 75px;
    top: 70px;
    width: 525px;
    height: 451px;
    background: var(--back-panel);
  }
  .back-content {
    position: absolute;
    left: 75px;
    top: 521px;
    width: 451px;
    height: 525px;
    transform: rotate(-90deg);
    transform-origin: top left;
    font-family: "Archivo Narrow", "Arial Narrow", sans-serif;
    color: var(--ink-grey);
  }
  .facts-box {
    position: absolute;
    left: 16px;
    top: 15px;
    width: 417px;
    height: 164px;
    box-sizing: border-box;
    border: 2px solid var(--oil-red);
    background: var(--page);
  }
  .facts-title {
    position: absolute;
    left: 14px;
    top: 10px;
    margin: 0;
    font-family: "Arimo", Arial, sans-serif;
    font-size: 20px;
    font-weight: 700;
  }
  .facts-list {
    position: absolute;
    left: 14px;
    top: 40px;
    margin: 0;
    padding: 0;
    list-style: none;
    font-size: 18px;
    line-height: 20px;
  }
  .grade-band {
    position: absolute;
    left: 0;
    bottom: 0;
    width: 100%;
    height: 32px;
    background: var(--oil-red);
    color: var(--ink-white);
    font-size: 18px;
    line-height: 32px;
    padding-left: 14px;
    box-sizing: border-box;
  }
  .back-text {
    position: absolute;
    left: 16px;
    width: 420px;
    margin: 0;
    font-size: 18.5px;
    line-height: 22px;
  }
  .company-address { top: 196px; }
  .usage-note { top: 261px; }
  .caution-note { top: 351px; }
  .caution-note strong { font-weight: 700; }

  .fold-line {
    position: absolute;
    left: 600px;
    top: 45px;
    width: 1px;
    height: 500px;
    background: var(--fold-line);
    z-index: 2;
  }
  .front-panel {
    position: absolute;
    left: 600px;
    top: 70px;
    width: 525px;
    height: 451px;
    background: var(--oil-red);
    color: var(--ink-white);
    overflow: hidden;
  }
  .oil-name {
    position: absolute;
    left: 0;
    top: 0;
    width: 330px;
    height: 340px;
    margin: 0;
    font-family: "Yellowtail", "Brush Script MT", cursive;
    font-weight: 400;
    line-height: 1;
  }
  .oil-name span {
    position: absolute;
    white-space: nowrap;
    transform: rotate(-8deg);
    transform-origin: left bottom;
  }
  .oil-name .line-one { left: 28px; top: 50px; font-size: 128px; }
  .oil-name .line-two { left: 14px; top: 170px; font-size: 140px; }
  .oil-descriptor {
    position: absolute;
    left: 333px;
    top: 46px;
    margin: 0;
    z-index: 1;
    font-family: "Lato", Arial, sans-serif;
    font-style: italic;
    font-weight: 900;
    font-size: 18px;
    line-height: 24px;
    text-transform: uppercase;
  }
  .front-rule {
    position: absolute;
    left: 0;
    top: 356px;
    width: 100%;
    height: 2px;
    background: var(--ink-white);
  }
  .bottle-size {
    position: absolute;
    left: 16px;
    top: 436px;
    transform: rotate(-90deg);
    transform-origin: top left;
    font-family: "Lato", Arial, sans-serif;
    font-weight: 700;
    font-size: 22px;
    line-height: 30px;
    white-space: nowrap;
  }
  .brand-name {
    position: absolute;
    left: 80px;
    top: 384px;
    display: flex;
    align-items: center;
    gap: 10px;
    font-family: "Lato", Arial, sans-serif;
    font-weight: 300;
    font-size: 33px;
    color: var(--logo-blush);
    white-space: nowrap;
  }
  .brand-dot {
    width: 9px;
    height: 9px;
    border-radius: 50%;
    background: var(--logo-blush);
  }
</style>
</head>
<body>
<main class="label">
  <section class="back-panel" aria-label="Label back"></section>
  <div class="back-content">
    <div class="facts-box">
      <h2 class="facts-title">Supplemental Facts</h2>
      <ul class="facts-list">
        <li>Serving Size: 1 drop</li>
        <li>Servings Per Container: About 250</li>
        <li>Oil: Rosmarinus Officinalis</li>
      </ul>
      <div class="grade-band">100% Pure Therapeutic Grade</div>
    </div>
    <p class="back-text company-address">Meadowlark Essentials<br>P.O. Box 402, Fairbrook, OR 97035</p>
    <p class="back-text usage-note">For aromatic, topical use. 100% pure therapeutic-grade essential oil. Dilute with a carrier oil before using.</p>
    <p class="back-text caution-note"><strong>CAUTION:</strong> For External Use Only. Not for Ingestion. Keep away from eyes and mucous membranes. May cause skin sensitivity. If pregnant consult physician before use. Keep out of reach of children. Keep away from flame.</p>
  </div>

  <div class="fold-line"></div>

  <section class="front-panel" aria-label="Label front">
    <h1 class="oil-name"><span class="line-one">Rose</span><span class="line-two">mary</span></h1>
    <p class="oil-descriptor">Rosmarinus<br>Officinalis<br>100% Pure<br>Essential Oil</p>
    <div class="front-rule"></div>
    <div class="bottle-size">15 ml</div>
    <div class="brand-name"><span>meadowlark</span><span class="brand-dot"></span><span>essentials</span></div>
  </section>
</main>
</body>
</html>
```